Business card for Sports Apparel business

DOUBLE SIDED DESIGN
We need business cards for a new sports apparel business. We are developing a protective headband for soccer initially.
Torvalle is focused on designing and developing head protection products to reduce the likelihood of concussion when playing sports. Exploring and understanding medical insights, material science research, current and former players experiences and governing bodies guidelines has allowed Torvalle to develop the safety, style, form and function requirements of a suitable product to bring to market.
Target Market(s)
Mums buying kits for the sons and daughters. Amateur footballers.
Industry/Entity Type
Sporting Good
Contact Information for Business Card
Martin Ashworth - CEO
Mobile: +44 7431589027
Email: martin@torvalle.co.uk
Tel: 0208 5519372
Helena Pargeter - COO
Mob: +44 7385 640117
Email: helena@torvalle.co.uk
Tel: 0208 5519372
Duncan Farrow - CCO
Mob: +44 7564 293081
Email: duncan@torvalle.co.uk
Tel: 0208 5519372
Look and feel
Each slider illustrates characteristics of the customer's brand and the style your logo design should communicate.

```html
<!DOCTYPE html>
<html lang="en">
<head>
<meta charset="utf-8">
<title>Torvalle Business Card</title>
<link href="https://fonts.googleapis.com/css2?family=Montserrat:wght@400;600;700&display=swap" rel="stylesheet">
<style>
  :root {
    --stage: #1f1f1f;
    --card: #676767;
    --ink: #ffffff;
    --ink-soft: #e6e6e6;
    --accent: #1f6fbf;
  }
  * { box-sizing: border-box; margin: 0; padding: 0; }
  html, body {
    width: 1200px; height: 900px; overflow: hidden;
    background: var(--stage);
    font-family: "Montserrat", sans-serif;
    color: var(--ink);
  }
  .stage {
    width: 1200px; height: 900px;
    display: flex; flex-direction: column;
    align-items: center; justify-content: center; gap: 40px;
  }
  .card {
    position: relative;
    width: 660px; height: 377px;
    background: var(--card);
    box-shadow: 0 12px 30px rgba(0,0,0,.45);
  }
  .card-front {
    display: flex; align-items: center; justify-content: center;
  }
  .wordmark {
    display: flex; align-items: center; gap: 14px;
    font-weight: 600; letter-spacing: .04em;
    color: var(--ink);
  }
  .wordmark .mark {
    background: var(--ink);
  }
  .card-front .wordmark { font-size: 56px; }
  .card-front .wordmark .mark { width: 22px; height: 22px; }

  .card-back .frame {
    position: absolute; inset: 38px 46px;
    border: 2px solid var(--accent);
    display: flex; align-items: center;
    padding: 0 40px;
  }
  .card-back .wordmark { font-size: 34px; }
  .card-back .wordmark .mark { width: 14px; height: 14px; }
  .divider {
    width: 1.5px; height: 130px;
    background: var(--ink-soft);
    margin: 0 24px 0 28px;
  }
  .person-name {
    font-weight: 700; font-size: 17px; letter-spacing: .06em;
    text-transform: uppercase;
  }
  .person-role {
    font-weight: 400; font-size: 15px; color: var(--ink-soft);
    margin-bottom: 16px;
  }
  .contact-list { list-style: none; }
  .contact-list li {
    display: flex; align-items: center; gap: 10px;
    font-size: 16px; line-height: 1.5; color: var(--ink-soft);
  }
  .contact-list svg {
    width: 14px; height: 14px; flex: none;
    fill: none; stroke: var(--ink-soft); stroke-width: 1.4;
  }
</style>
</head>
<body>
<main class="stage">
  <section class="card card-front" aria-label="Card front">
    <div class="wordmark"><span class="mark"></span><span>TORVALLE</span></div>
  </section>

  <section class="card card-back" aria-label="Card back">
    <div class="frame">
      <div class="wordmark"><span class="mark"></span><span>TORVALLE</span></div>
      <div class="divider"></div>
      <div class="details">
        <p class="person-name">Martin Ashworth</p>
        <p class="person-role">CEO</p>
        <ul class="contact-list">
          <li>
            <svg viewBox="0 0 14 14" aria-hidden="true"><rect x="4" y="1" width="6" height="12" rx="1"/><line x1="6" y1="11" x2="8" y2="11"/></svg>
            0208 551 9372
          </li>
          <li>
            <svg viewBox="0 0 14 14" aria-hidden="true"><path d="M2 2.5 L4.5 2 L6 5 L4.5 6.2 A7 7 0 0 0 7.8 9.5 L9 8 L12 9.5 L11.5 12 A10 10 0 0 1 2 2.5 Z"/></svg>
            +44 7431589027
          </li>
          <li>
            <svg viewBox="0 0 14 14" aria-hidden="true"><rect x="1" y="3" width="12" height="8"/><polyline points="1,3 7,8 13,3"/></svg>
            martin@torvalle.co.uk
          </li>
        </ul>
      </div>
    </div>
  </section>
</main>
</body>
</html>
```